RESIDENTIAL CONSTRUCTION

We are a company that specializes in building custom residential homes, the design should also emphasize that quality and service is our priority.

Industry/Entity Type

Construction Company

Contact Information for Business Card

Contact Person: Marcus Lindqvist
Company Address: 273 West Alder Ave San Jose , Ca 95380
Phone Number : 408-731-2946
Email Address: Stoneridgehomes517@mailvista.net

Font styles to use
Sans Serif

Colors
ec1f27

Requirements
Must have
• CSLB # 7362015
Nice to have
• needs to have same color as logo i uploaded, we will be printing these on a clear plastic card.

```html
<!DOCTYPE html>
<html lang="en">
<head>
<meta charset="UTF-8">
<title>Stoneridge Homes – Business Card</title>
<link rel="stylesheet" href="https://fonts.googleapis.com/css2?family=Oswald:wght@500;600&family=Lato:wght@400&display=swap">
<style>
  :root {
    --brand-red: #c01f2f;
    --stripe-black: #0d0d0d;
    --card-clear: #f7f6f6;
    --backdrop: #e4e2e0;
    --ink-white: #ffffff;
  }
  html, body {
    margin: 0;
    padding: 0;
    width: 1200px;
    height: 900px;
    overflow: hidden;
    background: var(--backdrop);
  }
  .business-card {
    position: absolute;
    left: 110px;
    top: 170px;
    width: 980px;
    height: 560px;
    background: var(--card-clear);
    box-shadow: 0 6px 24px rgba(0,0,0,0.12);
    overflow: hidden;
  }
  .card-panels {
    position: absolute;
    inset: 0;
  }
  .panel-red { fill: var(--brand-red); }
  .panel-stripe { fill: var(--stripe-black); }
  .contact-side {
    position: absolute;
    left: 40px;
    top: 0;
    width: 560px;
    height: 100%;
    color: var(--ink-white);
    font-family: "Lato", sans-serif;
  }
  .holder-name {
    position: absolute;
    top: 66px;
    margin: 0;
    font-family: "Oswald", sans-serif;
    font-weight: 600;
    font-size: 38px;
    letter-spacing: 0.5px;
    text-transform: uppercase;
  }
  .license-number,
  .office-address,
  .contact-line {
    position: absolute;
    margin: 0;
    font-size: 28px;
    line-height: 36px;
  }
  .license-number { top: 272px; }
  .office-address { top: 330px; }
  .contact-line {
    display: flex;
    align-items: center;
    gap: 10px;
  }
  .contact-phone { top: 430px; }
  .contact-email { top: 466px; }
  .contact-icon {
    width: 22px;
    height: 22px;
    fill: var(--ink-white);
    flex: none;
  }
  .company-mark {
    position: absolute;
    left: 500px;
    top: 84px;
    width: 430px;
    display: flex;
    align-items: center;
    justify-content: flex-end;
    gap: 16px;
  }
  .mark-square {
    width: 40px;
    height: 40px;
    background: var(--brand-red);
    flex: none;
  }
  .company-name {
    margin: 0;
    font-family: "Oswald", sans-serif;
    font-weight: 600;
    font-size: 62px;
    line-height: 1;
    color: var(--brand-red);
    text-transform: uppercase;
    white-space: nowrap;
  }
</style>
</head>
<body>
  <section class="business-card">
    <svg class="card-panels" width="980" height="560" viewBox="0 0 980 560" aria-hidden="true">
      <polygon class="panel-stripe" points="330,0 346,0 670,560 654,560"/>
      <polygon class="panel-red" points="0,0 332,0 656,560 0,560"/>
    </svg>

    <div class="contact-side">
      <h1 class="holder-name">Marcus Lindqvist</h1>
      <p class="license-number">CSLB # 7362015</p>
      <p class="office-address">273 West Alder Ave San Jose<br>Ca 95380</p>
      <p class="contact-line contact-phone">
        <svg class="contact-icon" viewBox="0 0 24 24" aria-hidden="true">
          <path d="M3 8c0-2 3-4 9-4s9 2 9 4v2h-5V8.5c-1-.6-2.4-.9-4-.9s-3 .3-4 .9V10H3z M6 12h12l2 8H4z M12 14.5a2.5 2.5 0 1 0 0 5a2.5 2.5 0 1 0 0-5z"/>
        </svg>
        408-731-2946
      </p>
      <p class="contact-line contact-email">
        <svg class="contact-icon" viewBox="0 0 24 24" aria-hidden="true">
          <path d="M2 5h20v14H2z M3.5 6.5 12 13l8.5-6.5z" fill-rule="evenodd"/>
        </svg>
        Stoneridgehomes517@mailvista.net
      </p>
    </div>

    <div class="company-mark">
      <span class="mark-square" aria-hidden="true"></span>
      <p class="company-name">Stoneridge Homes</p>
    </div>
  </section>
</body>
</html>
```